Lone Star Wetland Flora Stewardship Guild

We need to design the home page of this new website. We would like a fun website design for provides as a resource for members and information for potential members.
Please design so that we can see a portion of background on each side on the website.
I just need the final design files psd no coding needed.
Attached is their logo (colors are not 100% set in stone either so can mess with those as I did in the quick mockup attached)
Attached is a pdf newsletter they send out, you can get a feel for them and what they are about. The design is crappy and we are here to fix that going forward and we are starting with the website.
Here are some quick example websites (design style is open)
- I attached a quick mockup i did just for a content visual but by all means do what you want.
- http://www.brightpathleaders.example/
- http://www.civicunityhub.example/
- http://preview.webskinvault.example/show.php?cat=layouts&host=skinbazaar&temp=novaline
- http://www.meadowkeep.example/
- http://www.urbangleaners.example/
- http://www.projectcozyknit.example/
here are some of the other chapters website (pretty bad!)
and here are some of the others:
- http://www.dwrvcs.example/
- http://kwfg.example/
- http://www.blvcg.example/
Content Items that need to be included:
1. Logo
2. Menu - home, about, members, resources, events, membership, contact
3. Become a member - button or action
4. social links - chatterloop, workweave, clipstream
5. banner - that needs to explain their purpose "Promoting environmental stewardship through operations, research, education and outreach" (or this can be worked into the design)
6. Upcoming event (s)
7. Advertisement - members can place an ad on the website, this can be a placeholder for now
8. newsletter signup
9. advertise with us - this link can be in the footer
30-60 years of age, succesfull (household budgets of 120K+ men and women that live in texas.
Education

```html
<!DOCTYPE html>
<html lang="en">
<head>
<meta charset="utf-8">
<title>Lone Star Wetland Flora Stewardship Guild</title>
<link rel="stylesheet" href="https://fonts.googleapis.com/css2?family=Mulish:wght@400;600;700&display=swap">
<style>
:root{
  --navy:#0d3d8f;
  --navy-deep:#0b3680;
  --navy-light:#1a4ea8;
  --red:#e04a5a;
  --text:#555a60;
  --panel:#f2f2f2;
  --border:#dedede;
  --white:#ffffff;
  --sky-top:#2a63b8;
  --sky-mid:#c9dcef;
  --grass:#3f7a2f;
  --chatterloop:#3b5b9b;
  --chirpline:#2aa3dc;
  --workweave:#1c86c6;
  --feed:#f28a1c;
  --clipstream:#d9312b;
}
*{box-sizing:border-box;margin:0;padding:0}
html,body{width:1200px;height:1086px;overflow:hidden}
body{
  position:relative;
  font-family:"Mulish",sans-serif;
  color:var(--text);
  background:linear-gradient(180deg,var(--sky-top) 0,var(--sky-mid) 150px,#e8eef4 220px,var(--grass) 300px,#6e9bb8 400px,#dfe8ee 520px,#ffffff 640px);
}
.page{position:absolute;left:60px;top:0;width:1080px;height:958px;background:var(--white);border-top:3px solid var(--red)}
.abs{position:absolute}
.brand{left:76px;top:22px;width:170px;color:var(--navy);font-weight:700;font-size:30px;line-height:1;letter-spacing:1px}
.brand small{display:block;font-size:10px;letter-spacing:0;margin-top:8px;color:var(--navy)}
.social{display:flex;gap:9px}
.social span{display:block;border-radius:50%}
.top-social{left:740px;top:37px}
.top-social span{width:30px;height:30px}
.c-chat{background:var(--chatterloop)}.c-chirp{background:var(--chirpline)}.c-work{background:var(--workweave)}.c-feed{background:var(--feed)}.c-clip{background:var(--clipstream)}
.utility{left:952px;top:43px;font-size:13px;color:#444;display:flex;align-items:center;gap:8px}
.utility svg{display:block}
.nav{left:74px;top:104px;width:813px;height:50px;background:var(--navy)}
.nav a,.nav i{position:absolute;top:0;line-height:50px;color:var(--white);text-decoration:none;font-size:12.5px;font-weight:600;font-style:normal;white-space:nowrap}
.nav i{font-size:11px}
.join{left:887px;top:104px;width:239px;height:50px;background:var(--red);color:var(--white);font-size:18px;font-weight:600;display:flex;align-items:center;justify-content:center;letter-spacing:.3px}
.slider{left:74px;top:158px;width:1052px;height:428px;border:3px solid #ddd}
.slide-photo{width:100%;height:100%;background:linear-gradient(180deg,#cfe3ef 0,#5f9a3d 18%,#4c7d34 28%,#6b6a52 35%,#4a3f33 55%,#8fa85a 75%,#6f7d3c 100%)}
.caption{left:88px;top:326px;width:657px;height:75px;background:rgba(255,255,255,.9);color:var(--navy);font-size:22px;font-weight:600;line-height:30px;padding:7px 12px;white-space:nowrap}
.dots{left:562px;top:549px;display:flex;gap:7px}
.dots span{width:14px;height:14px;border-radius:50%;background:var(--white)}
.dots .on{background:var(--red)}
.card{top:622px;width:331px;height:306px;background:var(--panel);border:1px solid var(--border)}
.card h2{height:38px;background:var(--navy);color:var(--white);font-size:17px;font-weight:600;line-height:38px;padding-left:13px}
.card p{font-size:12.5px;line-height:21px}
.btn{position:absolute;left:13px;width:119px;height:33px;background:var(--red);color:var(--white);font-size:12.5px;line-height:33px;text-align:center}
.about{left:74px}
.about p{padding:11px 13px 0}
.events{left:434px}
.event{position:absolute;left:15px;width:300px}
.thumb{position:absolute;left:0;width:81px;height:75px}
.t1{background:linear-gradient(180deg,#b9d4e4,#4d7d3a 45%,#3f5a3a)}
.t2{background:linear-gradient(180deg,#6f8f78,#3f6a44 50%,#8faf63)}
.event p{position:absolute;left:95px;width:210px}
.more{display:block;color:var(--red);font-size:11.5px;margin-top:2px}
.advert{left:794px}
.ad{position:absolute;left:27px;top:52px;width:277px;height:230px;background:#3b3b3b;text-align:center;overflow:hidden}
.ad b{display:block;color:var(--white);font-size:42px;font-weight:600;line-height:47px;margin-top:22px}
.ad em{display:block;color:#e7c933;font-style:normal;font-size:19px;margin-top:10px}
.ad .band{position:absolute;left:0;bottom:0;width:100%;height:64px;background:#d9b928}
.footer{left:0;top:958px;width:1200px;height:128px;background:var(--navy-deep)}
.footer-right{left:700px;top:958px;width:500px;height:128px;background:var(--navy-light);clip-path:polygon(30px 0,100% 0,100% 100%,0 100%)}
.flinks{left:74px;top:982px;font-size:11.5px;color:var(--white);font-weight:600;white-space:nowrap}
.flinks i{font-style:normal;margin:0 6px}
.flinks .hl{color:var(--red)}
.legal{left:74px;top:1026px;font-size:11.5px;color:#b9c6e0;line-height:20px}
.fhead{top:982px;font-size:11.5px;color:var(--white);font-weight:600}
.signup{left:748px;top:1010px;display:flex}
.signup span{width:158px;height:28px;background:var(--white);font-size:11px;color:#888;line-height:28px;padding-left:11px}
.signup b{width:27px;height:28px;background:var(--red);display:flex;align-items:center;justify-content:center}
.foot-social{left:972px;top:1009px;gap:8px}
.foot-social span{width:25px;height:25px}
</style>
</head>
<body>
<div class="page"></div>

<div class="abs brand">LSWFSG<small>Lone Star Wetland Flora Stewardship Guild</small></div>

<div class="abs social top-social" aria-label="Social links">
  <span class="c-chat" title="chatterloop"></span><span class="c-chirp" title="chirpline"></span><span class="c-work" title="workweave"></span><span class="c-feed" title="feed"></span><span class="c-clip" title="clipstream"></span>
</div>

<div class="abs utility">
  <svg width="16" height="16" viewBox="0 0 16 16"><rect x="1" y="1" width="14" height="14" rx="2" fill="#555"/><path d="M5 4c0 4 3 7 7 8l1-2-2-1-1 1c-2-1-3-2-4-4l1-1-1-2z" fill="#fff"/></svg>
  <span>CONTACT</span><span style="margin:0 4px">|</span>
  <svg width="14" height="16" viewBox="0 0 14 16"><path d="M4 7V5a3 3 0 0 1 6 0v2" stroke="#555" stroke-width="2" fill="none"/><rect x="1" y="7" width="12" height="9" rx="1" fill="#555"/></svg>
  <span>LOG IN</span>
</div>

<nav class="abs nav">
  <a style="left:14px">HOME</a><i style="left:84px">|</i>
  <a style="left:112px">ABOUT</a><i style="left:188px">|</i>
  <a style="left:217px">MEMBERS</a><i style="left:310px">|</i>
  <a style="left:339px">RESOURCES</a><i style="left:444px">|</i>
  <a style="left:473px">EVENTS</a><i style="left:553px">|</i>
  <a style="left:582px">MEMBERSHIP</a><i style="left:695px">|</i>
  <a style="left:724px">CONTACT</a>
</nav>
<div class="abs join">BECOME A MEMBER</div>

<div class="abs slider"><div class="slide-photo" role="img" aria-label="Photo of a calm pond covered with lily pads, framed by green trees"></div></div>
<div class="abs caption">PROMOTING ENVIRONMENTAL STEWARDSHIP THROUGH<br>OPERATIONS, RESEARCH, EDUCATION AND OUTREACH</div>
<div class="abs dots"><span class="on"></span><span></span><span></span><span></span></div>

<section class="abs card about">
  <h2>ABOUT OUR COMPANY</h2>
  <p>Aliquam molestie, mi et imperdiet euismod, dui purus auctor tellus, et interdum lacus lectus et ante. Sed accumsan sollicitudin sapien, sit amet adipiscing turpis gravida ac. In congue, neque ac lobortis volutpat, libero mauris varius mi, vitae suscipit ipsum ligula vitae risus. Duis aliquam nibh a dui iaculis viverra id a velit. Aenean lacinia sodales eros, sit amet molestie enim consectetur eget. Sed vel magna vel eros adipiscing adipiscing...</p>
  <span class="btn" style="top:255px">READ MORE &nbsp;››</span>
</section>

<section class="abs card events">
  <h2>UPCOMING EVENTS</h2>
  <div class="event" style="top:53px">
    <div class="thumb t1" role="img" aria-label="Photo of a reed-lined pond"></div>
    <p>Aliquam molestie, mi et imperdiet euismod, dui purus auctor tellus, et interdum lacus lectus et ante.<span class="more">READ MORE ››</span></p>
  </div>
  <div class="event" style="top:156px">
    <div class="thumb t2" role="img" aria-label="Photo of water lilies and reeds"></div>
    <p>Aliquam molestie, mi et imperdiet euismod, dui purus auctor tellus, et interdum lacus lectus et ante.<span class="more">READ MORE ››</span></p>
  </div>
  <span class="btn" style="top:256px;left:14px">READ MORE &nbsp;››</span>
</section>

<section class="abs card advert">
  <h2>ADVERTISEMENT</h2>
  <div class="ad">
    <b>ADVERTISE<br>HERE</b>
    <em>CONTACT US NOW</em>
    <div class="band" role="img" aria-label="Yellow caution band"></div>
  </div>
</section>

<div class="abs footer"></div>
<div class="abs footer-right"></div>

<div class="abs flinks">HOME<i>/</i>ABOUT<i>/</i>MEMBERS<i>/</i>RESOURCES<i>/</i>EVENTS<i>/</i>MEMBERSHIP<i>/</i>CONTACT<i>/</i><span class="hl">ADVAERTISE WITH US</span></div>
<div class="abs legal">Copright © 2014. Company Name. All Right Reserved<br>Term of Services &nbsp;|&nbsp; Privacy Policy</div>

<div class="abs fhead" style="left:748px">NEWSLETTER SIGN UP</div>
<div class="abs signup"><span>Enter Email Address</span><b><svg width="10" height="12" viewBox="0 0 10 12"><path d="M2 1l6 5-6 5" stroke="#fff" stroke-width="2.5" fill="none"/></svg></b></div>

<div class="abs fhead" style="left:974px">CONNECT US</div>
<div class="abs social foot-social" aria-label="Social links">
  <span class="c-chat" title="chatterloop"></span><span class="c-chirp" title="chirpline"></span><span class="c-work" title="workweave"></span><span class="c-feed" title="feed"></span><span class="c-clip" title="clipstream"></span>
</div>
</body>
</html>
```